Cool Website Design Gleam Shell Crew.

We need a new website, using our existing domain, with a similar function to https://www.marbeckfilm.com/ or https://www.tolvanfinishworks.com/ instagram gleam_shell.crew.
We can send google docs with pictures.
Logo attached

```html
<!DOCTYPE html>
<html lang="en">
<head>
<meta charset="utf-8">
<title>Gleam Shell Crew – Premium Vehicle Wraps in Calgary</title>
<link rel="stylesheet" href="https://fonts.googleapis.com/css2?family=Bebas+Neue&family=Roboto:wght@400;500;700&display=swap">
<style>
:root{
  --bg:#000;
  --bg-soft:#0a0a0c;
  --card:#050505;
  --purple:#6a2ee6;
  --violet:#5b35e8;
  --blue:#3a55e6;
  --accent:#4c3fe2;
  --white:#fff;
  --muted:#d9d9d9;
  --grad:linear-gradient(90deg,#6a2ee6,#3a5ae6);
}
*{margin:0;padding:0;box-sizing:border-box}
html,body{width:1200px;height:4773px;overflow:hidden;background:var(--bg);color:var(--white);font-family:"Roboto",Arial,sans-serif}
.page{position:relative;width:1200px;height:4773px;overflow:hidden}
.abs{position:absolute}
.display{font-family:"Bebas Neue",Impact,sans-serif;font-weight:400;letter-spacing:1px}
.accent{color:var(--accent)}
.btn{position:absolute;display:flex;align-items:center;justify-content:center;color:#fff;font-size:14px;font-weight:700;background:var(--grad);clip-path:polygon(6% 0,100% 0,94% 100%,0 100%)}
/* header */
.brand{position:absolute;left:122px;top:24px;font-family:"Bebas Neue",Impact,sans-serif;font-size:30px;color:var(--violet);letter-spacing:1px}
.brand-box{position:absolute;left:122px;top:62px;width:26px;height:26px;background:var(--violet)}
.nav{position:absolute;top:38px;left:384px;display:flex;gap:0;font-size:15px}
.nav a{color:#fff;text-decoration:none;position:absolute;white-space:nowrap}
.nav a.active{color:#4d7cff}
.nav a.active::after{content:"";position:absolute;left:0;right:0;bottom:-8px;height:3px;background:#3a6ae6}
/* hero */
.hero{position:absolute;left:0;top:0;width:1200px;height:880px;background:radial-gradient(ellipse at 60% 30%,#15161c 0%,#060608 60%,#000 100%)}
.hero-title{position:absolute;top:160px;width:100%;text-align:center;font-size:66px}
.hero-sub{position:absolute;top:255px;width:100%;text-align:center;font-size:23px;font-weight:700}
/* testimonials */
.section-title{position:absolute;width:100%;text-align:center;font-size:52px}
.review{position:absolute;top:1046px;width:302px;height:311px;background:var(--card);border-radius:6px;padding:24px 20px}
.review.featured{background:linear-gradient(180deg,#3e4fe4,#7a2fe8)}
.avatar{position:absolute;left:20px;top:17px;width:56px;height:56px;border-radius:50%;background:#7a5a48}
.review .name{position:absolute;left:90px;top:24px;font-size:14px;font-weight:700}
.review .stars{position:absolute;left:90px;top:46px;display:flex;gap:3px;align-items:center}
.review .quote{position:absolute;right:16px;top:22px;font-family:"Bebas Neue",sans-serif;font-size:56px;line-height:40px;color:var(--violet)}
.review.featured .quote{color:#fff}
.review p{position:absolute;left:20px;right:20px;top:96px;font-size:13px;line-height:30px;color:#eee}
.arrow{position:absolute;width:28px;height:28px;border-radius:50%;display:flex;align-items:center;justify-content:center}
/* about */
.about{position:absolute;left:0;top:1454px;width:1200px;height:496px;background:#000}
.body-copy{font-size:13px;line-height:35px;color:#eee}
/* services */
.services{position:absolute;left:0;top:1950px;width:1200px;height:620px;background:var(--bg-soft)}
.svc-label{position:absolute;font-size:19px;font-weight:500;white-space:nowrap}
.svc-icon{position:absolute;width:80px;height:80px;border-radius:50%;background:linear-gradient(135deg,#3a55e6,#6a2ee6);display:flex;align-items:center;justify-content:center}
/* protect */
.protect{position:absolute;left:0;top:2570px;width:1200px;height:517px;background:#000}
/* gallery */
.gallery-item{position:absolute;width:315px;height:294px;border-radius:4px}
/* footer */
.footer-col h4{font-family:"Bebas Neue",sans-serif;font-weight:400;font-size:20px;letter-spacing:1px;margin-bottom:8px}
.footer-col a{display:block;color:#fff;text-decoration:none;font-size:12px;line-height:26px}
.contact-row{position:absolute;left:891px;display:flex;align-items:center;gap:18px;font-size:12px}
.social{position:absolute;top:4655px;width:28px;height:28px;border-radius:50%;background:#fff}
</style>
</head>
<body>
<div class="page">

  <!-- HERO -->
  <section class="hero">
    <div class="abs" role="img" aria-label="Hatchback in a cyan wrap with black claw-stripe graphics" style="left:185px;top:426px;width:843px;height:389px;border-radius:45% 45% 30% 30% / 60% 60% 25% 25%;background:radial-gradient(ellipse at 45% 55%,#35d6dc 0%,#1fb2bb 45%,#0d1a1c 80%,rgba(0,0,0,0) 100%)"></div>
    <svg class="abs" style="left:0;top:0" width="1200" height="880" aria-hidden="true">
      <polygon points="0,815 300,772 300,782 0,830" fill="#5b2ee0"/>
      <polygon points="1018,672 1200,646 1200,662 1018,688" fill="#5b2ee0"/>
    </svg>
    <div class="hero-title display">PREMIUM <span class="accent">VEHICLE WRAPS</span> IN CALGARY</div>
    <div class="hero-sub">Quality craftsmanship. Modern designs. Guaranteed finish.</div>
    <div class="btn" style="left:504px;top:316px;width:190px;height:40px">GET A FREE QUOTE</div>
  </section>

  <!-- HEADER -->
  <div class="brand">GLEAM SHELL CREW</div>
  <div class="brand-box"></div>
  <nav class="nav">
    <a class="active" style="left:2px">HOME</a>
    <a style="left:80px">ABOUT</a>
    <a style="left:164px">SERVICES</a>
    <a style="left:266px">BLOG</a>
    <a style="left:343px">PRODUCTS</a>
    <a style="left:440px">FAQ's</a>
    <a style="left:516px">Gallery</a>
  </nav>
  <div class="btn" style="left:976px;top:24px;width:126px;height:42px">CONTACT</div>

  <!-- TESTIMONIALS -->
  <h2 class="section-title display" style="top:935px">WHAT&nbsp; OUR <span class="accent">CUSTOMERS SAY?</span></h2>

  <div class="review" style="left:111px">
    <div class="avatar"></div><div class="name">Nora .K</div>
    <div class="stars"><svg width="104" height="14"><circle cx="7" cy="7" r="6" fill="none" stroke="#4a7ae6" stroke-width="2"/><g fill="#e0a526"><polygon points="24,1 26,6 31,6 27,9 29,14 24,11 19,14 21,9 17,6 22,6"/><polygon points="40,1 42,6 47,6 43,9 45,14 40,11 35,14 37,9 33,6 38,6"/><polygon points="56,1 58,6 63,6 59,9 61,14 56,11 51,14 53,9 49,6 54,6"/><polygon points="72,1 74,6 79,6 75,9 77,14 72,11 67,14 69,9 65,6 70,6"/><polygon points="88,1 90,6 95,6 91,9 93,14 88,11 83,14 85,9 81,6 86,6"/></g></svg></div>
    <div class="quote">“</div>
    <p>“From the first message to pickup day, the process was seamless. They helped me choose the right colour and the result was better than I expected. Couldn't be happier.”</p>
  </div>
  <div class="review featured" style="left:448px">
    <div class="avatar" style="background:#5a6a5a"></div><div class="name">Theo .B</div>
    <div class="stars"><svg width="104" height="14"><circle cx="7" cy="7" r="6" fill="none" stroke="#fff" stroke-width="2"/><g fill="#e0a526"><polygon points="24,1 26,6 31,6 27,9 29,14 24,11 19,14 21,9 17,6 22,6"/><polygon points="40,1 42,6 47,6 43,9 45,14 40,11 35,14 37,9 33,6 38,6"/><polygon points="56,1 58,6 63,6 59,9 61,14 56,11 51,14 53,9 49,6 54,6"/><polygon points="72,1 74,6 79,6 75,9 77,14 72,11 67,14 69,9 65,6 70,6"/><polygon points="88,1 90,6 95,6 91,9 93,14 88,11 83,14 85,9 81,6 86,6"/></g></svg></div>
    <div class="quote">“</div>
    <p>“Honest, transparent, and extremely talented. My car looks brand new and the craftsmanship is top-tier. I won't go anywhere else.”</p>
  </div>
  <div class="review" style="left:785px">
    <div class="avatar" style="background:#8a6a50"></div><div class="name">Lena.W</div>
    <div class="stars"><svg width="104" height="14"><circle cx="7" cy="7" r="6" fill="none" stroke="#4a7ae6" stroke-width="2"/><g fill="#e0a526"><polygon points="24,1 26,6 31,6 27,9 29,14 24,11 19,14 21,9 17,6 22,6"/><polygon points="40,1 42,6 47,6 43,9 45,14 40,11 35,14 37,9 33,6 38,6"/><polygon points="56,1 58,6 63,6 59,9 61,14 56,11 51,14 53,9 49,6 54,6"/><polygon points="72,1 74,6 79,6 75,9 77,14 72,11 67,14 69,9 65,6 70,6"/><polygon points="88,1 90,6 95,6 91,9 93,14 88,11 83,14 85,9 81,6 86,6"/></g></svg></div>
    <div class="quote">“</div>
    <p>“I've wrapped several vehicles before and this is by far the cleanest job I've ever seen. Zero imperfections and the finish is buttery smooth. If you care about your car, this is the place.”</p>
  </div>
  <div class="arrow" style="left:36px;top:1179px;background:var(--violet)"><svg width="12" height="12"><polyline points="8,2 4,6 8,10" fill="none" stroke="#fff" stroke-width="2"/></svg></div>
  <div class="arrow" style="left:1125px;top:1179px;background:#fff"><svg width="12" height="12"><polyline points="4,2 8,6 4,10" fill="none" stroke="#000" stroke-width="2"/></svg></div>

  <!-- ABOUT -->
  <section class="about">
    <h2 class="abs display" style="left:111px;top:76px;font-size:52px">ABOUT <span class="accent">US</span></h2>
    <p class="abs body-copy" style="left:114px;top:152px;width:446px;text-align:justify">Lorem ipsum dolor sit amet, consectetur adipiscing elit, sed do eiusmod tempor incididunt ut labore et dolore magna aliqua. Ut enim ad minim veniam, quis nostrud exercitation ullamco laboris nisi ut aliquip ex ea commodo consequat. Duis aute irure dolor in reprehenderit in voluptate velit esse cillum dolore eu fugiat nulla pariatur.</p>
    <div class="btn" style="left:118px;top:361px;width:130px;height:40px">READ MORE</div>
    <svg class="abs" style="left:550px;top:0" width="650" height="496" aria-hidden="true"><polygon points="148,0 158,0 18,496 0,496" fill="#3a4fe6"/></svg>
    <div class="abs" role="img" aria-label="Close-up of a glossy blue wrapped car door and mirror" style="left:570px;top:0;width:630px;height:496px;clip-path:polygon(24% 0,100% 0,100% 100%,0 100%);background:linear-gradient(135deg,#0f1f50 0%,#1f4fd0 40%,#2a66e8 60%,#0d2a80 100%)"></div>
  </section>

  <!-- SERVICES -->
  <section class="services">
    <h2 class="section-title display" style="top:76px;font-size:52px">OUR <span class="accent">SERVICES</span></h2>
    <svg class="abs" style="left:0;top:0" width="1200" height="620" aria-hidden="true" fill="none" stroke="#6a2ee6" stroke-width="3" stroke-dasharray="7 7">
      <path d="M372,278 Q350,330 352,345"/>
      <path d="M360,420 Q370,460 400,475"/>
      <path d="M840,278 Q860,320 850,345"/>
      <path d="M840,420 Q830,460 800,485"/>
    </svg>
    <div class="abs" style="left:398px;top:263px;width:380px;height:148px;display:flex;align-items:center;justify-content:center;gap:14px">
      <span style="width:40px;height:40px;border-radius:50%;background:var(--grad)"></span>
      <span class="display" style="font-size:50px;color:var(--violet)">GLEAM SHELL CREW</span>
    </div>

    <div class="svc-label" style="right:874px;top:216px">Paint Protection Film</div>
    <div class="svc-icon" style="left:340px;top:195px"><svg width="34" height="34" viewBox="0 0 34 34"><path d="M17 3 L29 8 V17 C29 24 23 29 17 31 C11 29 5 24 5 17 V8 Z" fill="none" stroke="#fff" stroke-width="2.5"/></svg></div>
    <div class="svc-label" style="right:915px;top:375px">Vinyl Wraps</div>
    <div class="svc-icon" style="left:306px;top:338px"><svg width="34" height="34" viewBox="0 0 34 34"><rect x="6" y="9" width="22" height="16" rx="2" fill="none" stroke="#fff" stroke-width="2.5"/><line x1="10" y1="17" x2="24" y2="17" stroke="#fff" stroke-width="2.5"/></svg></div>
    <div class="svc-label" style="right:850px;top:503px">Window Tinting</div>
    <div class="svc-icon" style="left:375px;top:458px"><svg width="34" height="34" viewBox="0 0 34 34"><path d="M6 8 H24 L29 16 V27 H6 Z" fill="none" stroke="#fff" stroke-width="2.5"/><line x1="6" y1="16" x2="29" y2="16" stroke="#fff" stroke-width="2.5"/></svg></div>

    <div class="svc-icon" style="left:788px;top:199px"><svg width="34" height="34" viewBox="0 0 34 34"><path d="M5 22 L9 13 H25 L29 22 V27 H5 Z" fill="none" stroke="#fff" stroke-width="2.5"/><circle cx="11" cy="22" r="2" fill="#fff"/><circle cx="23" cy="22" r="2" fill="#fff"/></svg></div>
    <div class="svc-label" style="left:885px;top:224px">Coloured PPF</div>
    <div class="svc-icon" style="left:806px;top:334px"><svg width="34" height="34" viewBox="0 0 34 34"><circle cx="17" cy="17" r="12" fill="none" stroke="#fff" stroke-width="2.5"/><path d="M11 18 L17 12 L23 18" fill="none" stroke="#fff" stroke-width="2.5"/></svg></div>
    <div class="svc-label" style="left:902px;top:362px">Pro Detailing</div>
    <div class="svc-icon" style="left:745px;top:458px"><svg width="34" height="34" viewBox="0 0 34 34"><path d="M4 24 L8 16 H26 L30 24 V28 H4 Z" fill="none" stroke="#fff" stroke-width="2.5"/><circle cx="17" cy="9" r="4" fill="#fff"/></svg></div>
    <div class="svc-label" style="left:843px;top:488px">Ceramic Coating</div>
  </section>

  <!-- PROTECT -->
  <section class="protect">
    <div class="abs" role="img" aria-label="Red performance SUV front three-quarter view in a dark studio" style="left:0;top:40px;width:640px;height:440px;background:radial-gradient(ellipse at 40% 55%,#b3121c 0%,#6a0a10 35%,#1a0d0e 65%,#000 100%)"></div>
    <svg class="abs" style="left:520px;top:0" width="160" height="517" aria-hidden="true"><polygon points="10,32 22,32 146,462 134,462" fill="#3a4fe6"/></svg>
    <h2 class="abs display accent" style="left:685px;top:62px;font-size:52px">PROTECT YOUR PAINT</h2>
    <h2 class="abs display" style="left:685px;top:126px;font-size:52px">LOOK GOOD DOING IT</h2>
    <p class="abs body-copy" style="left:686px;top:208px;width:402px;text-align:justify">Lorem ipsum dolor sit amet, consectetur adipiscing elit, sed do eiusmod tempor incididunt ut labore et dolore magna aliqua. Ut enim ad minim veniam, quis nostrud exercitation ullamco laboris nisi ut aliquip ex ea commodo consequat.</p>
    <div class="btn" style="left:689px;top:372px;width:156px;height:42px">WRAP MY CAR</div>
  </section>

  <!-- GALLERY -->
  <h2 class="section-title display" style="top:3174px">WRAP <span class="accent">GALLERY</span></h2>
  <div class="gallery-item" role="img" aria-label="Silver hatchback front view" style="left:111px;top:3265px;background:linear-gradient(160deg,#8a9098,#3c4046 60%,#1a1c1e)"></div>
  <div class="gallery-item" role="img" aria-label="Blue sedan with windshield decal in a garage" style="left:441px;top:3265px;background:linear-gradient(160deg,#3a3a40,#1e2e5a 55%,#101418)"></div>
  <div class="gallery-item" role="img" aria-label="Grey car with black hood wrap in a workshop" style="left:770px;top:3265px;background:linear-gradient(160deg,#5a5a5e,#2a2a2c 55%,#141416)"></div>
  <div class="gallery-item" role="img" aria-label="Silver sedan with black racing stripes" style="left:111px;top:3574px;background:linear-gradient(160deg,#6a6a6e,#3a3c40 55%,#141416)"></div>
  <div class="gallery-item" role="img" aria-label="Blue pickup truck parked outdoors" style="left:441px;top:3574px;background:linear-gradient(160deg,#b8bcc0,#1e3580 55%,#2a2c30)"></div>
  <div class="gallery-item" role="img" aria-label="White car with side graphics outdoors" style="left:770px;top:3574px;background:linear-gradient(160deg,#9ab6d8,#c8cacc 50%,#4a4c4e)"></div>
  <div class="gallery-item" role="img" aria-label="Bright blue hatchback with windshield banner" style="left:111px;top:3891px;background:linear-gradient(160deg,#8a8c90,#1a78d8 50%,#0e2a5a)"></div>
  <div class="gallery-item" role="img" aria-label="Red coupe with grey hood stripes" style="left:441px;top:3891px;background:linear-gradient(160deg,#3a3a3c,#c0101a 50%,#2a0a0c)"></div>
  <div class="gallery-item" role="img" aria-label="Silver sedan on a gravel lot" style="left:770px;top:3891px;background:linear-gradient(160deg,#9ab0c8,#9a9ca0 50%,#5a5a5c)"></div>

  <!-- FOOTER BAND -->
  <svg class="abs" style="left:0;top:4230px" width="1200" height="200" aria-hidden="true"><polygon points="0,186 1200,8 1200,22 0,200" fill="#2f5ee0"/><polygon points="0,200 1200,22 1200,200" fill="#050505"/></svg>

  <!-- FOOTER -->
  <footer>
    <div class="abs display" style="left:122px;top:4483px;font-size:44px;color:var(--violet)">GLEAM SHELL CREW</div>
    <div class="abs" style="left:122px;top:4540px;width:40px;height:40px;background:var(--grad)"></div>
    <div class="social" style="left:129px;background:var(--violet)"></div>
    <div class="social" style="left:164px"></div>
    <div class="social" style="left:199px"></div>
    <div class="social" style="left:234px"></div>

    <div class="abs footer-col" style="left:506px;top:4468px">
      <h4>QUICK LINKS</h4>
      <a>Home</a><a>About</a><a>Services</a><a>Blog</a><a>Products</a><a>FAQ's</a><a>Contact Us</a>
    </div>
    <div class="abs footer-col" style="left:678px;top:4468px">
      <h4>OTHER LINKS</h4>
      <a>Privacy Policy</a><a>Terms &amp; Conditions</a><a>Diclaimer</a><a>Support</a><a>Help</a>
    </div>
    <div class="abs footer-col" style="left:891px;top:4468px"><h4>CONTACT INFO</h4></div>
    <div class="contact-row" style="top:4516px"><svg width="22" height="22" viewBox="0 0 22 22"><path d="M11 2 C6 2 4 6 4 9 C4 14 11 20 11 20 C11 20 18 14 18 9 C18 6 16 2 11 2 Z" fill="#fff"/><circle cx="11" cy="9" r="3" fill="#000"/></svg><span>Lorem Ipsum,USA -437916</span></div>
    <div class="contact-row" style="top:4563px"><svg width="22" height="22" viewBox="0 0 22 22"><circle cx="11" cy="11" r="10" fill="#fff"/><path d="M7 6 L9 6 L10 9 L8.5 10 C9.5 12 10 12.5 12 13.5 L13 12 L16 13 L16 15 C12 16 6 10 7 6 Z" fill="#000"/></svg><span>+1 555 014 2290</span></div>
    <div class="contact-row" style="top:4610px"><svg width="22" height="22" viewBox="0 0 22 22"><circle cx="11" cy="11" r="10" fill="#fff"/><rect x="5.5" y="7.5" width="11" height="7" fill="none" stroke="#000" stroke-width="1.5"/><polyline points="5.5,7.5 11,11.5 16.5,7.5" fill="none" stroke="#000" stroke-width="1.5"/></svg><span>info@gleamshellcrew.com</span></div>

    <div class="abs" style="left:111px;top:4732px;width:976px;height:1px;background:#444"></div>
    <div class="abs" style="left:0;top:4742px;width:1200px;text-align:center;font-size:13px">© 2025 Gleam Shell Crew.All rights reserved</div>
  </footer>

</div>
</body>
</html>
```